Business card design for my company.
I would like the card's background colour to be black. You can also see our web site to get an idea of our brand. https://www.tmwhomecrafting.com.au/
- Name
- Email

```html
<!DOCTYPE html>
<html lang="en">
<head>
<meta charset="utf-8">
<title>TMW Home Crafting – Business Card</title>
<link rel="stylesheet" href="https://fonts.googleapis.com/css2?family=Montserrat:wght@400;500;700&display=swap">
<style>
  :root {
    --stage: #2b2b2b;
    --card: #151515;
    --card-edge: #0c0c0c;
    --green: #12a14a;
    --white: #f2f2f2;
    --soft: #d8d8d8;
    --font: "Montserrat", Arial, sans-serif;
  }
  * { box-sizing: border-box; margin: 0; padding: 0; }
  html, body { width: 1200px; height: 689px; overflow: hidden; }
  body {
    background: var(--stage);
    font-family: var(--font);
    position: relative;
  }
  .card {
    position: absolute;
    top: 185px;
    width: 520px;
    height: 318px;
    border-radius: 22px;
    background: var(--card);
    overflow: hidden;
    box-shadow: 0 12px 30px rgba(0,0,0,0.45);
  }
  .card--back { left: 50px; }
  .card--front { left: 630px; }

  /* back side */
  .back-pattern {
    position: absolute;
    inset: 0;
    background: linear-gradient(100deg, #bdbdbd 0%, #7a7a7a 25%, #2a2a2a 50%, #101010 75%, #0a0a0a 100%);
  }
  .back-brand {
    position: absolute;
    left: 50%;
    top: 50%;
    transform: translate(-50%, -50%);
    display: flex;
    align-items: center;
    gap: 8px;
    padding: 10px 16px;
    background: var(--card);
    border-radius: 6px;
  }
  .back-brand__mark { width: 12px; height: 12px; background: var(--green); }
  .back-brand__name {
    font-weight: 700;
    font-size: 18px;
    color: var(--white);
    letter-spacing: 0.5px;
  }

  /* front side */
  .brand {
    position: absolute;
    left: 40px;
    top: 58px;
    display: flex;
    align-items: center;
    gap: 12px;
  }
  .brand__mark { width: 26px; height: 26px; background: var(--green); }
  .brand__name {
    font-weight: 700;
    font-size: 30px;
    line-height: 1.05;
    color: var(--white);
  }
  .person {
    position: absolute;
    right: 40px;
    top: 40px;
    text-align: right;
  }
  .person__name {
    font-weight: 700;
    font-size: 24px;
    color: var(--green);
  }
  .person__role {
    font-weight: 400;
    font-size: 14px;
    color: var(--white);
    margin-top: 4px;
  }
  .person-bar {
    position: absolute;
    right: 0;
    top: 42px;
    width: 10px;
    height: 44px;
    background: var(--green);
  }
  .contact {
    position: absolute;
    left: 40px;
    bottom: 34px;
    list-style: none;
  }
  .contact__item {
    display: flex;
    align-items: center;
    gap: 10px;
    font-size: 14px;
    color: var(--soft);
    line-height: 1;
    margin-top: 10px;
  }
  .contact__item--address { margin-bottom: 14px; }
  .contact__icon { width: 14px; height: 14px; flex: none; }
</style>
</head>
<body>

  <section class="card card--back" aria-label="Card back">
    <div class="back-pattern" role="img" aria-label="Repeating company emblem pattern in silver fading to black"></div>
    <div class="back-brand">
      <span class="back-brand__mark"></span>
      <span class="back-brand__name">TMW Home Crafting</span>
    </div>
  </section>

  <section class="card card--front" aria-label="Card front">
    <div class="brand">
      <span class="brand__mark"></span>
      <span class="brand__name">TMW<br>Home Crafting</span>
    </div>

    <div class="person">
      <p class="person__name">Liam Harcourt</p>
      <p class="person__role">General Manager</p>
    </div>
    <span class="person-bar"></span>

    <ul class="contact">
      <li class="contact__item contact__item--address">
        <svg class="contact__icon" viewBox="0 0 24 24"><path fill="#12a14a" d="M12 2a7 7 0 0 0-7 7c0 5 7 13 7 13s7-8 7-13a7 7 0 0 0-7-7zm0 9.5A2.5 2.5 0 1 1 12 6.5a2.5 2.5 0 0 1 0 5z"/></svg>
        Launceston, Tasmania, Australia
      </li>
      <li class="contact__item">
        <svg class="contact__icon" viewBox="0 0 24 24"><path fill="#12a14a" d="M6.6 10.8a15 15 0 0 0 6.6 6.6l2.2-2.2a1 1 0 0 1 1-.25 11.4 11.4 0 0 0 3.6.57 1 1 0 0 1 1 1V20a1 1 0 0 1-1 1A17 17 0 0 1 3 4a1 1 0 0 1 1-1h3.5a1 1 0 0 1 1 1c0 1.25.2 2.45.57 3.6a1 1 0 0 1-.25 1z"/></svg>
        0400 123 456
      </li>
      <li class="contact__item">
        <svg class="contact__icon" viewBox="0 0 24 24"><path fill="#12a14a" d="M2 5h20v14H2zm2 2v.4l8 5 8-5V7l-8 5z"/></svg>
        info@tmwhomecrafting.com.au
      </li>
      <li class="contact__item">
        <svg class="contact__icon" viewBox="0 0 24 24"><circle cx="12" cy="12" r="9" fill="none" stroke="#12a14a" stroke-width="2"/><path d="M3 12h18M12 3c3 3 3 15 0 18M12 3c-3 3-3 15 0 18" fill="none" stroke="#12a14a" stroke-width="1.6"/></svg>
        www.tmwhomecrafting.com.au
      </li>
    </ul>
  </section>

</body>
</html>
```